VFX Company Business Card Design Project

The Kestrel Works is a decentralized Visual Effects Studio servicing the television and feature film industries.
Project Brief:
Take our logo that was previously designed on Pencil Harbor and make a double sided business card.
Requirements:
- Card MUST be double sided.
- Front of card MUST have the yellow part of our logo against the dark grey background.
- Back of card is completely up to the designer.
- Back of card must include the complete company logo.
Please follow these File Preparation guidelines:
http://printnook.ca/infopage?file=filetype_en&s=PrintNook_new&lang=en
Business

```html
<!DOCTYPE html>
<html lang="en">
<head>
<meta charset="utf-8">
<title>The Kestrel Works – Business Cards</title>
<link rel="stylesheet" href="https://fonts.googleapis.com/css2?family=Josefin+Sans:wght@400;700&family=Libre+Baskerville:wght@400;700&display=swap">
<style>
:root{
  --backdrop:#8c4a24;
  --charcoal:#262626;
  --charcoal-soft:#2c2c2c;
  --paper:#eaefe5;
  --slate:#5f6b6e;
  --slate-light:#6f7c80;
  --sun:#fcc62a;
  --ink:#222222;
  --white:#ffffff;
}
*{margin:0;padding:0;box-sizing:border-box}
html,body{width:1200px;height:733px;overflow:hidden}
body{background:var(--backdrop);position:relative;font-family:"Josefin Sans",sans-serif}
.card{position:absolute;width:523px;height:298px;border-radius:28px;overflow:hidden;box-shadow:0 2px 6px rgba(0,0,0,.35)}
.card--front{left:70px;top:44px;background:var(--charcoal)}
.card--contact{left:631px;top:48px;background:var(--paper)}
.card--light{left:67px;top:385px;background:var(--paper)}
.card--slate{left:625px;top:389px;background:var(--slate)}

.brand{position:absolute;left:0;right:0;text-align:center;font-family:"Josefin Sans",sans-serif;font-weight:700;letter-spacing:1px;white-space:nowrap}
.card--front .brand{top:122px;font-size:50px;color:var(--sun)}
.card--light .brand{top:122px;font-size:46px;color:var(--ink)}
.card--slate .brand{top:122px;font-size:46px;color:var(--white)}
.brand-dot{display:inline-block;width:22px;height:22px;border-radius:50%;background:currentColor;margin-right:14px;vertical-align:4px}

.web{position:absolute;left:0;right:0;bottom:24px;text-align:center;font-size:18px;letter-spacing:2.5px}
.card--light .web{color:var(--ink)}
.card--slate .web{color:var(--white)}

.contact-art{position:absolute;inset:0}
.holder{position:absolute;top:8px;left:0;right:0;text-align:center;font-family:"Libre Baskerville",serif;color:var(--paper);font-size:17px;font-weight:700}
.holder small{font-size:13px;font-weight:400}
.card--contact .brand{top:74px;font-size:38px;color:var(--paper)}
.address{position:absolute;right:296px;top:238px;text-align:right;font-family:"Libre Baskerville",serif;font-size:13px;line-height:20px;color:#333}
.divider{position:absolute;left:242px;top:234px;width:1px;height:46px;background:#9aa0a0}
.lines{position:absolute;left:256px;top:218px;list-style:none;font-family:"Libre Baskerville",serif;font-size:13px;line-height:19.5px;color:#333}
.lines li{display:flex;align-items:center;gap:6px}
.lines svg{width:11px;height:11px;flex:none}
</style>
</head>
<body>

<section class="card card--front" aria-label="Card front">
  <div class="brand">The Kestrel Works</div>
</section>

<section class="card card--contact" aria-label="Card back with contact details">
  <svg class="contact-art" viewBox="0 0 523 298" preserveAspectRatio="none" aria-hidden="true">
    <path d="M0 0H523V148Q400 215 260 204Q120 194 0 118Z" fill="var(--charcoal-soft)"/>
    <path d="M0 112Q150 186 300 196Q360 200 428 190Q330 208 250 204Q110 194 0 132Z" fill="var(--slate-light)"/>
  </svg>
  <div class="holder">Your Name, <small>Title</small></div>
  <div class="brand">The Kestrel Works</div>
  <div class="address">00, Complex name<br>City, State 0042</div>
  <div class="divider"></div>
  <ul class="lines">
    <li><svg viewBox="0 0 12 12"><path d="M2 1l3 1-1 2 4 4 2-1 1 3-2 1C5 11 1 7 1 3z" fill="#333"/></svg>0987 654321</li>
    <li><svg viewBox="0 0 12 12"><rect x="3" y="1" width="6" height="10" rx="1" fill="#333"/><rect x="4" y="2.5" width="4" height="6" fill="var(--paper)"/></svg>0987 654321</li>
    <li><svg viewBox="0 0 12 12"><rect x="1" y="3" width="10" height="7" fill="#333"/><path d="M1 3l5 4 5-4" stroke="var(--paper)" fill="none"/></svg>info@kestrelworks.com</li>
    <li><svg viewBox="0 0 12 12"><circle cx="6" cy="6" r="5" fill="none" stroke="#333"/><path d="M1 6h10M6 1v10" stroke="#333"/></svg>www.kestrelworks.com</li>
  </ul>
</section>

<section class="card card--light" aria-label="Card back, light version">
  <div class="brand"><span class="brand-dot"></span>The Kestrel Works</div>
  <div class="web">www.kestrelworks.com</div>
</section>

<section class="card card--slate" aria-label="Card back, slate version">
  <div class="brand">The Kestrel Works</div>
  <div class="web">www.kestrelworks.com</div>
</section>

</body>
</html>
```